Investment company needing business card

We are wanting a business card which looks sharp and easy on the eye. We are thinking of having a business card with the logo embossed on it, to really make it stand out. We will only have a small amount of information of the business card, person's name, position, email address and phone number

Contact Information for Business Card

Danielle Frost
Executive Assistant
+64 21 473 5162
danielf@harwickpartners.co.nz

Requirements
Must have
• Embossed logo
Should not have
• Not to be busy

```html
<!DOCTYPE html>
<html lang="en">
<head>
<meta charset="utf-8">
<title>Harwick Partners – Business Card</title>
<link rel="stylesheet" href="https://fonts.googleapis.com/css2?family=Source+Sans+3:wght@400;700&display=swap">
<style>
  :root {
    --page-bg: #e9e6e3;
    --card-white: #ffffff;
    --brand-green: #1fa463;
    --slate: #646466;
    --slate-dark: #58585a;
    --slate-deep: #4e4e50;
    --rule-grey: #8c8c8c;
    --text-grey: #555555;
    --web-light: #c9c9c9;
  }
  * { box-sizing: border-box; margin: 0; padding: 0; }
  html, body {
    width: 1200px; height: 997px; overflow: hidden;
    background: var(--page-bg);
    font-family: "Source Sans 3", "Myriad Pro", Arial, sans-serif;
  }
  .card {
    position: absolute; left: 320px;
    width: 560px; height: 320px;
    box-shadow: 0 2px 8px rgba(0,0,0,.12);
    overflow: hidden;
  }
  /* Front */
  .card-front { top: 150px; background: var(--card-white); }
  .edge-band {
    position: absolute; right: 0; top: 0; width: 20px; height: 100%;
    background: var(--slate);
  }
  .edge-accent {
    position: absolute; right: 0; top: 78px; width: 20px; height: 34px;
    background: var(--brand-green);
  }
  .brand-front {
    position: absolute; left: 40px; top: 58px;
    display: flex; align-items: center; gap: 10px;
  }
  .brand-mark { width: 26px; height: 26px; background: var(--brand-green); }
  .brand-name {
    font-weight: 700; font-size: 25px; letter-spacing: 1px;
    text-transform: uppercase; color: var(--brand-green);
  }
  .header-rule {
    position: absolute; left: 40px; right: 40px; top: 112px;
    height: 1px; background: var(--rule-grey);
  }
  .contact { position: absolute; left: 40px; top: 176px; color: var(--text-grey); }
  .person-name {
    font-weight: 700; font-size: 17px; letter-spacing: .5px;
    text-transform: uppercase; color: var(--brand-green);
    padding-bottom: 3px; border-bottom: 1px solid var(--rule-grey);
    width: 230px;
  }
  .person-role { font-size: 14px; margin: 4px 0 8px; }
  .contact-line {
    display: flex; align-items: center; gap: 9px;
    font-size: 14px; line-height: 20px;
  }
  .contact-line svg { width: 11px; height: 11px; fill: var(--brand-green); flex: none; }
  /* Back */
  .card-back { top: 527px; background: var(--slate); }
  .brand-back {
    position: absolute; left: 0; right: 0; top: 118px;
    display: flex; justify-content: center; align-items: center; gap: 12px;
  }
  .brand-back .brand-mark { background: var(--slate-deep); width: 30px; height: 30px; }
  .brand-back .brand-name { color: var(--slate-deep); font-size: 30px; }
  .back-rule {
    position: absolute; left: 150px; right: 150px; top: 182px;
    height: 1px; background: var(--slate-dark);
  }
  .back-web {
    position: absolute; left: 0; right: 0; bottom: 46px;
    text-align: center; color: var(--web-light);
    font-size: 14px; letter-spacing: 1.5px;
  }
  .back-web-rule {
    position: absolute; left: 140px; right: 140px; bottom: 38px;
    height: 1px; background: var(--slate-dark);
  }
</style>
</head>
<body>
  <section class="card card-front">
    <div class="edge-band"></div>
    <div class="edge-accent"></div>
    <div class="brand-front">
      <span class="brand-mark"></span>
      <span class="brand-name">Harwick Partners</span>
    </div>
    <div class="header-rule"></div>
    <div class="contact">
      <p class="person-name">Danielle Frost</p>
      <p class="person-role">Executive Assistant</p>
      <p class="contact-line">
        <svg viewBox="0 0 12 12" aria-hidden="true"><path d="M2.5 0.5 L4.5 0.5 L5.5 3.5 L4 4.5 Q5 7 7.5 8 L8.5 6.5 L11.5 7.5 L11.5 9.5 Q11 11.5 9 11.5 Q0.5 10 0.5 2.5 Q0.5 0.8 2.5 0.5 Z"/></svg>
        +64 21 473 5162
      </p>
      <p class="contact-line">
        <svg viewBox="0 0 12 12" aria-hidden="true"><path d="M0.5 2 H11.5 V10 H0.5 Z M1.5 3 L6 6.5 L10.5 3 Z" fill-rule="evenodd"/></svg>
        danielf@harwickpartners.co.nz
      </p>
      <p class="contact-line">
        <svg viewBox="0 0 12 12" aria-hidden="true"><path d="M6 0.5 A5.5 5.5 0 1 0 6 11.5 A5.5 5.5 0 1 0 6 0.5 Z M6 2 A4 4 0 1 1 6 10 A4 4 0 1 1 6 2 Z" fill-rule="evenodd"/><rect x="2" y="5.4" width="8" height="1.2"/><rect x="5.4" y="2" width="1.2" height="8"/></svg>
        www.harwickpartners.co.nz
      </p>
    </div>
  </section>

  <section class="card card-back">
    <div class="brand-back">
      <span class="brand-mark"></span>
      <span class="brand-name">Harwick Partners</span>
    </div>
    <div class="back-rule"></div>
    <p class="back-web">www.harwickpartners.co.nz</p>
    <div class="back-web-rule"></div>
  </section>
</body>
</html>
```